IT Company that provides secure IT solutions and services to our customers

We need business cards and a logo for a new IT Solutions company just created based in Kuala Lumpur, Malaysia. But will also be serving other countries in the region. We provide secure data, voice solutions on mobile platforms. Our first offering is encrypted voice and data solutions for IOS, Android, Windows and BlackBerry devices.

Target Market(s)

large organizations Govt, Police, Defence, Anti-corruption, Legal, highly regulated industries such as Health-care, Financial, Banking, Insurance,

Industry/Entity Type

Information Technology

Contact Information for Business Card

VelmoraNet (Logo - colour is ORVEX blue)Roshan Adeel Managing Director Kryption IT Sdn. Bhd.5th Floor, Block D, Wisma PLB,No.14 Jalan Seri Melor,50470, Kuala LumpurMalaysia

Font styles to use
Sans Serif

Colors
3176b5
ec1f27
fbed22

Requirements
Must have
• VelmoraNet all in Blue like ORVEX blue. A logo design perhaps a play of VN, K with a dangling T (colour can be any)
Nice to have
• I want a clean crisp card, not too busy, easy to read.

```html
<!DOCTYPE html>
<html lang="en">
<head>
<meta charset="utf-8">
<title>VelmoraNet — Business Card</title>
<link href="https://fonts.googleapis.com/css2?family=Arimo:wght@400;700&display=swap" rel="stylesheet">
<style>
  :root {
    --backdrop: #a0a0a0;
    --card: #ffffff;
    --ink: #231f20;
  }
  * { margin: 0; padding: 0; box-sizing: border-box; }
  html, body {
    width: 1200px;
    height: 1000px;
    overflow: hidden;
    background: var(--backdrop);
    font-family: "Arimo", Arial, sans-serif;
  }
  .card {
    position: absolute;
    left: 58px;
    top: 183px;
    width: 1085px;
    height: 634px;
    background: var(--card);
    color: var(--ink);
  }
  .brand {
    position: absolute;
    left: 285px;
    top: 133px;
    display: flex;
    align-items: center;
    gap: 26px;
  }
  .brand-mark {
    width: 146px;
    height: 146px;
    flex: none;
  }
  .brand-name {
    font-weight: 700;
    font-size: 100px;
    line-height: 1;
    letter-spacing: -3px;
    color: var(--ink);
  }
  .person {
    position: absolute;
    left: 549px;
    top: 318px;
  }
  .person-name {
    font-weight: 700;
    font-size: 35px;
    letter-spacing: 3px;
    line-height: 1;
    text-transform: uppercase;
  }
  .person-role {
    margin-top: 14px;
    font-weight: 400;
    font-size: 30px;
    letter-spacing: 1px;
    line-height: 1;
  }
</style>
</head>
<body>
  <main class="card">
    <div class="brand">
      <svg class="brand-mark" viewBox="0 0 146 146" aria-hidden="true">
        <circle cx="73" cy="73" r="73" fill="var(--ink)"/>
      </svg>
      <span class="brand-name">VelmoraNet</span>
    </div>
    <div class="person">
      <p class="person-name">Roshan Adeel</p>
      <p class="person-role">Managing Director</p>
    </div>
  </main>
</body>
</html>
```